Company identity deisgn should support 2 languages

I would like to get our company identity design
This includes the following only
Business Cards 2 languages Arabic and English
Email signature
Letterhead
Linkedin profile images
Attached is the logo in Ai format

Requirements
Must have
• For business card
Must have
Name and Adrees in arabic
Name and Address in english
You might use both side of the card
Should not have
• Any pictures other than the logo

```html
<!DOCTYPE html>
<html lang="en">
<head>
<meta charset="utf-8">
<title>Lumen Cognitive Systems – Letterhead</title>
<link href="https://fonts.googleapis.com/css2?family=Open+Sans:wght@400;600&family=Roboto:wght@400&display=swap" rel="stylesheet">
<style>
  :root {
    --backdrop: #e2e2e2;
    --paper: #f9f9f9;
    --ink: #3a3a3a;
    --ink-soft: #555555;
    --brand-blue: #1d70b8;
    --watermark: #e3ecf3;
    --signature-tone: #ececec;
  }
  * { margin: 0; padding: 0; box-sizing: border-box; }
  html, body {
    width: 1200px; height: 800px; overflow: hidden;
    background: var(--backdrop);
  }
  .letterhead {
    position: absolute;
    left: 327px; top: 20px;
    width: 546px; height: 760px;
    background: var(--paper);
    overflow: hidden;
    font-family: "Open Sans", sans-serif;
    color: var(--ink);
  }
  .brand {
    position: absolute; left: 49px; top: 62px;
    display: flex; align-items: center; gap: 8px;
  }
  .brand-dot {
    width: 18px; height: 18px; border-radius: 50%;
    background: var(--brand-blue);
  }
  .brand-name {
    font-family: "Open Sans", sans-serif;
    font-weight: 600; font-size: 14px; letter-spacing: 0.6px;
    color: var(--brand-blue);
  }
  .letter-body {
    position: absolute; left: 49px; top: 175px; width: 446px;
    font-size: 10.2px; line-height: 14.7px;
  }
  .salutation { margin-bottom: 14.7px; }
  .letter-body p.paragraph {
    text-align: justify; margin-bottom: 14.7px;
  }
  .closing { position: absolute; left: 49px; top: 484px; font-size: 10.2px; }
  .signature {
    position: absolute; left: 49px; top: 512px;
    width: 64px; height: 62px;
    background: var(--signature-tone);
    border-radius: 4px;
  }
  .contact {
    position: absolute; left: 49px; top: 637px;
    font-family: "Roboto", sans-serif;
    font-size: 13px; line-height: 15.5px;
    color: var(--ink-soft);
  }
  .contact .address { margin-bottom: 3px; }
  .contact-line { display: flex; align-items: center; gap: 4px; line-height: 16.3px; }
  .contact-line svg { width: 11px; height: 11px; flex: none; }
  .watermark {
    position: absolute; right: -40px; bottom: -70px;
    width: 240px; height: 240px; border-radius: 50%;
    background: var(--watermark); opacity: 0.7;
  }
</style>
</head>
<body>
  <main class="letterhead">
    <header class="brand">
      <span class="brand-dot"></span>
      <span class="brand-name">LUMEN COGNITIVE SYSTEMS</span>
    </header>

    <section class="letter-body">
      <p class="salutation">Dear customer,</p>
      <p class="paragraph">Lorem ipsum dolor sit amet, consectetur adipisicing elit, sed do eiusmod tempor incididunt ut labore et dolore magna aliqua. Ut enim ad minim veniam, quis nostrud exercitation ullamco laboris nisi ut aliquip ex ea commodo consequat. Duis aute irure dolor in reprehenderit in voluptate velit esse cillum dolore eu fugiat nulla pariatur. Excepteur sint occaecat cupidatat non proident, sunt in culpa qui officia deserunt mollit anim id est laborum.</p>
      <p class="paragraph">Lorem ipsum dolor sit amet, consectetur adipisicing elit, sed do eiusmod tempor incididunt ut labore et dolore magna aliqua. Ut enim ad minim veniam, quis nostrud exercitation ullamco laboris nisi ut aliquip ex ea commodo consequat. Duis aute irure dolor in reprehenderit in voluptate velit esse cillum dolore eu fugiat nulla pariatur. Excepteur sint occaecat cupidatat non proident, sunt in culpa qui officia deserunt mollit anim id est laborum.</p>
      <p class="paragraph">Lorem ipsum dolor sit amet, consectetur adipisicing elit, sed do eiusmod tempor incididunt ut labore et dolore magna aliqua. Ut enim ad minim veniam, quis nostrud exercitation ullamco laboris nisi ut aliquip ex ea commodo consequat. Duis aute irure dolor in reprehenderit in voluptate velit esse cillum dolore eu fugiat nulla pariatur. Excepteur sint occaecat cupidatat non proident, sunt in culpa qui officia deserunt mollit anim id est laborum.</p>
    </section>

    <p class="closing">Yours Sincerely,</p>
    <div class="signature" role="img" aria-label="Handwritten signature of the sender"></div>

    <div class="watermark"></div>

    <footer class="contact">
      <p class="address">42 Harbour Lane, Vernon<br>B.C. Canada V1T 2K8</p>
      <p class="contact-line">
        <svg viewBox="0 0 12 12" aria-hidden="true"><path fill="#1d70b8" d="M1 4.5C1 3 3 2 6 2s5 1 5 2.5V5H8.5V4H3.5v1H1z M3 6h6l1.5 4.5h-9z"/><circle cx="6" cy="8" r="1.3" fill="#f9f9f9"/></svg>
        604.555.0142
      </p>
      <p class="contact-line">
        <svg viewBox="0 0 12 12" aria-hidden="true"><rect x="0.5" y="2.5" width="11" height="7.5" fill="#1d70b8"/><path d="M0.8 3l5.2 4 5.2-4" stroke="#f9f9f9" stroke-width="1" fill="none"/></svg>
        hello@lumenmail.com
      </p>
      <p class="contact-line">
        <svg viewBox="0 0 12 12" aria-hidden="true"><circle cx="6" cy="6" r="5.5" fill="#1d70b8"/><ellipse cx="6" cy="6" rx="2.3" ry="5.2" fill="none" stroke="#f9f9f9" stroke-width="0.8"/><line x1="0.6" y1="6" x2="11.4" y2="6" stroke="#f9f9f9" stroke-width="0.8"/></svg>
        www.lumenweb.com
      </p>
    </footer>
  </main>
</body>
</html>
```